Business Card Design for Occupational Medicine Start Up Company

We need to design a professional business card. We are a healthcare company providing occupational medicine services to blue collar industries. We are professional, efficient and high quality service providers.

Target Market(s)

Blue Collar Industry: Shipbuilding, Ports, Trucking Companies; The Executives and Safety Officers for these companies

Industry/Entity Type

Healthcare

Contact Information for Business Card

Logo, Name, Title, Email, Phone

Other font styles liked:
• Please match our Brand Guide

Requirements
Must have
• Our Company Colors and Logo

```html
<!DOCTYPE html>
<html lang="en">
<head>
<meta charset="utf-8">
<title>CrewWell Business Card</title>
<link href="https://fonts.googleapis.com/css2?family=Lato:wght@400;700;900&family=Montserrat:wght@600&display=swap" rel="stylesheet">
<style>
  :root {
    --stage: #2b2b2b;
    --paper: #ffffff;
    --card-dark: #232323;
    --navy: #233a8f;
    --sky: #2ba8e0;
    --amber: #f2b24a;
    --ink-soft: #7a7a7a;
    --ink: #333a4a;
  }
  * { margin: 0; padding: 0; box-sizing: border-box; }
  html, body {
    width: 1200px; height: 929px; overflow: hidden;
    background: var(--stage);
    font-family: "Lato", sans-serif;
  }
  .card {
    position: absolute; left: 320px;
    width: 560px; height: 320px;
    border-radius: 18px; overflow: hidden;
  }
  .card-front { top: 110px; background: var(--paper); }
  .card-back { top: 499px; background: var(--card-dark); }

  .brand-mark {
    position: absolute; top: 34px; left: 0; right: 0;
    text-align: center;
    font-family: "Lato", sans-serif; font-weight: 900;
    font-size: 30px; color: var(--navy); letter-spacing: 0.5px;
  }
  .identity { position: absolute; left: 44px; top: 140px; }
  .identity-name { font-weight: 900; font-size: 31px; color: var(--navy); }
  .identity-title { font-size: 17px; color: var(--ink-soft); margin-top: 2px; }

  .address {
    position: absolute; left: 44px; top: 224px;
    display: flex; gap: 10px; align-items: flex-start;
    font-size: 16px; line-height: 1.3; color: var(--ink);
  }
  .contact-list {
    position: absolute; right: 40px; top: 122px;
    list-style: none; font-size: 16px; color: var(--ink); line-height: 1.45;
  }
  .contact-list li { display: flex; align-items: center; gap: 10px; }
  .icon { width: 15px; height: 15px; flex: none; fill: var(--navy); }

  .color-band {
    position: absolute; left: 0; right: 0; bottom: 0; height: 9px;
    display: flex;
  }
  .band-navy { flex: 45; background: var(--navy); }
  .band-sky { flex: 32; background: var(--sky); }
  .band-amber { flex: 23; background: var(--amber); }

  .back-wordmark {
    position: absolute; inset: 0;
    display: flex; align-items: center; justify-content: center;
    font-family: "Montserrat", sans-serif; font-weight: 600;
    font-size: 46px; letter-spacing: 3px; color: #ffffff;
  }
</style>
</head>
<body>
  <section class="card card-front">
    <div class="brand-mark">CrewWell</div>

    <div class="identity">
      <h1 class="identity-name">Marcus Deland</h1>
      <p class="identity-title">Account Executive</p>
    </div>

    <div class="address">
      <svg class="icon" viewBox="0 0 24 24"><path d="M12 2a7 7 0 0 0-7 7c0 5 7 13 7 13s7-8 7-13a7 7 0 0 0-7-7zm0 9.5A2.5 2.5 0 1 1 12 6.5a2.5 2.5 0 0 1 0 5z"/></svg>
      <p>48 Wharf Road Suite 210<br>Portside, CA 90210</p>
    </div>

    <ul class="contact-list">
      <li><svg class="icon" viewBox="0 0 24 24"><path d="M6.6 10.8a15 15 0 0 0 6.6 6.6l2.2-2.2c.3-.3.7-.4 1-.2 1.1.4 2.3.6 3.6.6.6 0 1 .4 1 1V20c0 .6-.4 1-1 1A17 17 0 0 1 3 4c0-.6.4-1 1-1h3.5c.6 0 1 .4 1 1 0 1.3.2 2.5.6 3.6.1.3 0 .7-.2 1z"/></svg>555.210.4482</li>
      <li><svg class="icon" viewBox="0 0 24 24"><path d="M6 2h12v5H6zM3 8h18v9h-3v5H6v-5H3zm5 7v5h8v-5z"/></svg>555.210.4490</li>
      <li><svg class="icon" viewBox="0 0 24 24"><path d="M2 5h20v14H2zm2 2v.5l8 5 8-5V7z"/></svg>mdeland@harborline.com</li>
      <li><svg class="icon" viewBox="0 0 24 24"><path d="M12 2a10 10 0 1 0 0 20 10 10 0 0 0 0-20zm6.9 9h-3a15 15 0 0 0-1.3-5.6A8 8 0 0 1 18.9 11zM12 4.1c.9 1.3 1.8 3.6 2 6.9h-4c.2-3.3 1.1-5.6 2-6.9zM9.4 5.4A15 15 0 0 0 8.1 11h-3a8 8 0 0 1 4.3-5.6zM5.1 13h3a15 15 0 0 0 1.3 5.6A8 8 0 0 1 5.1 13zm6.9 6.9c-.9-1.3-1.8-3.6-2-6.9h4c-.2 3.3-1.1 5.6-2 6.9zm2.6-1.3a15 15 0 0 0 1.3-5.6h3a8 8 0 0 1-4.3 5.6z"/></svg>www.harborline.com</li>
    </ul>

    <div class="color-band">
      <span class="band-navy"></span>
      <span class="band-sky"></span>
      <span class="band-amber"></span>
    </div>
  </section>

  <section class="card card-back">
    <div class="back-wordmark">CREWWELL</div>
  </section>
</body>
</html>
```